Stylish business cards for KV7

To create an appealing and professional business card design for a WOMEN Owned Construction Supply Company.
2 sided card. Incorporate brand elements, curvy, colorful, sleek and bright. No solid white background. attached samples of styles added shapes/ribbons. Want something with that WOW that looks awesome, factor. It is a new logo, so feel free to mess with logo colors in the blue and teal factors that can look good with both dark and light background. If you want to try a watermark with just the KV7, without the "Supply" that might look cool to.

Industry/Entity Type

Women owned construction supply company

Contact Information for Business Card

Name, Title, and phone number and email, web page. maybe spot for qr code.

Font styles to use
Sans Serif

Requirements
Nice to have
• would love to see colors, maybe stylish ribbon dividers or some sort of 2 or 3 tone color card that compliments logo.
Should not have
• Please do not have all white background. Do not include Home/reale state/ or building images.

```html
<!DOCTYPE html>
<html lang="en">
<head>
<meta charset="utf-8">
<title>KV7 Supply – Business Cards</title>
<link rel="stylesheet" href="https://fonts.googleapis.com/css2?family=Poppins:wght@400;500;700&display=swap">
<style>
  :root {
    --bg: #2b2b2d;
    --card-black: #0b0b0c;
    --white: #ffffff;
    --ink: #0d1a2e;
    --blue: #0c4a80;
    --teal: #2a9cc8;
  }
  * { margin: 0; padding: 0; box-sizing: border-box; }
  html, body { width: 1200px; height: 875px; overflow: hidden; }
  body {
    background: var(--bg);
    font-family: "Poppins", sans-serif;
    position: relative;
  }
  .card {
    position: absolute;
    top: 287px;
    width: 525px;
    height: 300px;
    border-radius: 18px;
    overflow: hidden;
    box-shadow: 0 18px 40px rgba(0,0,0,.45);
  }
  .card--front { left: 40px; background: var(--card-black); }
  .card--back { left: 635px; background: var(--white); }

  .brand-name {
    position: absolute;
    font-family: "Poppins", sans-serif;
    font-weight: 500;
    white-space: nowrap;
    display: flex;
    align-items: center;
    gap: 10px;
    line-height: 1;
  }
  .card--front .brand-name {
    left: 0; right: 0; top: 0; bottom: 0;
    justify-content: center;
    font-size: 52px;
    color: var(--teal);
  }
  .card--back .brand-name {
    right: 50px; top: 62px;
    font-size: 32px;
    color: var(--ink);
  }
  .brand-dot {
    width: 14px; height: 14px; border-radius: 50%;
    background: currentColor;
  }
  .card--back .brand-dot { width: 10px; height: 10px; }

  .wave { position: absolute; inset: 0; width: 100%; height: 100%; }

  .holder {
    position: absolute;
    left: 0; top: 108px;
    display: flex; align-items: flex-start; gap: 14px;
  }
  .holder-mark { width: 22px; height: 22px; background: var(--ink); margin-top: 2px; }
  .holder-name {
    font-weight: 700; font-size: 20px; color: var(--ink);
    letter-spacing: .3px; line-height: 1.1;
  }
  .holder-title { font-size: 11px; color: var(--ink); margin-top: 3px; }

  .contact {
    position: absolute;
    left: 80px; bottom: 16px;
    color: var(--white);
    font-size: 10.5px;
    line-height: 1.45;
  }
  .contact-address { margin-bottom: 6px; }
  .contact-list { list-style: none; }
  .contact-list li { display: flex; align-items: center; gap: 8px; }
  .contact-list svg { width: 10px; height: 10px; fill: var(--white); flex: none; }
</style>
</head>
<body>

  <section class="card card--front" aria-label="Card front">
    <div class="brand-name"><span class="brand-dot"></span>KV7 Supply</div>
  </section>

  <section class="card card--back" aria-label="Card back">
    <svg class="wave" viewBox="0 0 525 300" preserveAspectRatio="none" aria-hidden="true">
      <defs>
        <linearGradient id="waveFill" x1="0" y1="1" x2="1" y2="0">
          <stop offset="0" stop-color="#061a33"/>
          <stop offset=".6" stop-color="#0a3a6a"/>
          <stop offset="1" stop-color="#0c4f86"/>
        </linearGradient>
      </defs>
      <path d="M0,300 L0,262 C20,215 80,180 190,172 C300,165 420,160 470,130 C500,110 515,85 525,65 L525,300 Z" fill="url(#waveFill)"/>
      <path d="M230,180 C330,173 430,166 478,142 C505,124 518,100 525,84" fill="none" stroke="#ffffff" stroke-width="3"/>
      <path d="M430,150 C480,132 510,98 520,56 C524,82 508,120 470,142 Z" fill="#0d1a2e"/>
    </svg>

    <div class="brand-name"><span class="brand-dot"></span>KV7 Supply</div>

    <div class="holder">
      <span class="holder-mark"></span>
      <div>
        <p class="holder-name">DANIEL BROOKS</p>
        <p class="holder-title">Managing Director</p>
      </div>
    </div>

    <div class="contact">
      <p class="contact-address">48 Harbor Point Drive<br>Lakeview, OR 97630 USA</p>
      <ul class="contact-list">
        <li><svg viewBox="0 0 10 10"><path d="M2 0.5 L3.8 2.6 L2.9 3.7 C3.6 5 4.9 6.3 6.3 7.1 L7.4 6.2 L9.5 8 L8.3 9.5 C4.5 9 1 5.5 0.5 1.7 Z"/></svg>+1.555.010.284</li>
        <li><svg viewBox="0 0 10 10"><path d="M0 2 H10 V8.5 H0 Z M0.6 2.4 L5 5.6 L9.4 2.4 L9.4 2.6 L5 6.2 L0.6 2.6 Z" fill-rule="evenodd"/></svg>hello@kv7supply.com</li>
        <li><svg viewBox="0 0 10 10"><circle cx="5" cy="5" r="4.5"/></svg>www.kv7supply.com</li>
      </ul>
    </div>
  </section>

</body>
</html>
```